I have a logo and need to design the business card and stationery.
Updates

The uploaded logo image named as GREYMARSH CONSTRUCTION which is to be replaced to GREYMARSH CONTRACTS. Kindly add below details and submit the designs- Company name- Greymarsh Engineering Contracts LLP Name & Post- Kelvan Joshi (Designated Partner) Address- Block No.317, Wing C, Tulvo Trade Court, Manek Pural Road, Ruparel Industrial Estate, Goregaon(E), Mumbai - 400 063 Contact- +91 97415 60382 Email- kelvanjoshi@mailbrook.example Website- www.greymarshcontracts.example Contact for Letterhead- +91-22-28754193

Hi Tovin Rahul, We are liking your Design #28860835. We have suggested some changes which are mentioned in feedback. Kindly revert with it asap to finalize this design.

Colors

Designer to choose colors to be used in the design.

```html
<!DOCTYPE html>
<html lang="en">
<head>
<meta charset="utf-8">
<title>Greymarsh Contracts – Business Card</title>
<link rel="stylesheet" href="https://fonts.googleapis.com/css2?family=Oswald:wght@500&family=Montserrat:wght@400&family=Roboto:wght@400&display=swap">
<style>
  :root {
    --backdrop: #4a4a4a;
    --card-light: #ffffff;
    --card-dark: #333333;
    --ink: #2e2e2e;
    --ink-soft: #3a3a3a;
    --mark: #1b1b1b;
    --rule: #4d4d4d;
  }
  * { margin: 0; padding: 0; box-sizing: border-box; }
  html, body { width: 1135px; height: 1200px; overflow: hidden; }
  body { background: var(--backdrop); position: relative; }

  .card {
    position: absolute;
    left: 205px;
    width: 726px;
    height: 414px;
  }
  .card--front { top: 145px; background: var(--card-light); }
  .card--back { top: 641px; background: var(--card-dark); }

  /* Front */
  .identity {
    position: absolute;
    left: 36px;
    top: 176px;
    width: 234px;
  }
  .identity__name {
    font-family: "Oswald", sans-serif;
    font-weight: 500;
    font-size: 41px;
    line-height: 41px;
    letter-spacing: 1.2px;
    color: var(--ink);
    white-space: nowrap;
  }
  .identity__role {
    margin-top: 1px;
    font-family: "Montserrat", sans-serif;
    font-weight: 400;
    font-size: 18px;
    letter-spacing: 1px;
    color: var(--ink);
    white-space: nowrap;
  }
  .divider {
    position: absolute;
    left: 293px;
    top: 108px;
    width: 1.5px;
    height: 204px;
    background: var(--rule);
  }
  .details {
    position: absolute;
    left: 322px;
    top: 104px;
    font-family: "Roboto", sans-serif;
    color: var(--ink-soft);
  }
  .address {
    font-size: 15.5px;
    line-height: 21px;
    white-space: nowrap;
    letter-spacing: 0.2px;
  }
  .address + .address { margin-top: 7px; }
  .contact-list { list-style: none; margin-top: 7px; }
  .contact-list li {
    display: flex;
    align-items: center;
    font-size: 17.5px;
    line-height: 24.5px;
    letter-spacing: 0.3px;
    white-space: nowrap;
    color: var(--ink);
  }
  .contact-list svg { width: 12px; height: 12px; margin-right: 7px; flex: none; }

  /* Back */
  .brand {
    position: absolute;
    left: 0;
    top: 106px;
    width: 100%;
    text-align: center;
  }
  .brand__square {
    display: block;
    width: 123px;
    height: 123px;
    margin: 0 auto;
    background: var(--mark);
  }
  .brand__name {
    margin-top: 24px;
    font-family: "Roboto", sans-serif;
    font-weight: 400;
    font-size: 32px;
    line-height: 1;
    letter-spacing: 2px;
    color: var(--mark);
    white-space: nowrap;
  }
  .tagline {
    position: absolute;
    left: 0;
    top: 357px;
    width: 100%;
    text-align: center;
    font-family: "Roboto", sans-serif;
    font-size: 23px;
    color: var(--mark);
    letter-spacing: 0.3px;
  }
</style>
</head>
<body>

<section class="card card--front" aria-label="Business card front">
  <div class="identity">
    <div class="identity__name">KELVAN JOSHI</div>
    <div class="identity__role">DESIGNATED PARTNER</div>
  </div>
  <div class="divider"></div>
  <div class="details">
    <p class="address">317, Tulvo Trade Court, Ruparel Industrial Estate,<br>Off Manek Pural Road, Goregaon East,<br>Mumbai – 400 063, Maharashtra, India</p>
    <p class="address">317, Wing C, Tulvo Trade Court, Manek Pural Road,<br>Ruparel Industrial Estate, Goregaon(E),<br>Mumbai - 400 063, Maharashtra, India</p>
    <ul class="contact-list">
      <li>
        <svg viewBox="0 0 12 12" aria-hidden="true"><path d="M2.3 0.8 L4.2 0.6 L5 3.3 L3.8 4.2 Q4.6 6.6 6.9 8 L8 6.9 L10.8 7.8 L10.6 9.9 Q9.9 11.4 8.3 11 Q2.8 9.2 1 3.6 Q0.7 1.5 2.3 0.8 Z" fill="#2e2e2e"/></svg>
        +91 9741560382
      </li>
      <li>
        <svg viewBox="0 0 12 12" aria-hidden="true"><rect x="0.8" y="2.3" width="10.4" height="7.4" fill="none" stroke="#2e2e2e" stroke-width="1.1"/><path d="M0.8 2.6 L6 6.4 L11.2 2.6" fill="none" stroke="#2e2e2e" stroke-width="1.1"/></svg>
        kelvan@greymarshcontracts.example
      </li>
      <li>
        <svg viewBox="0 0 12 12" aria-hidden="true"><g fill="none" stroke="#555" stroke-width="0.9"><circle cx="6" cy="6" r="5.2"/><ellipse cx="6" cy="6" rx="2.3" ry="5.2"/><path d="M0.8 6 H11.2 M1.6 3.3 H10.4 M1.6 8.7 H10.4"/></g></svg>
        www.greymarshcontracts.example
      </li>
    </ul>
  </div>
</section>

<section class="card card--back" aria-label="Business card back">
  <div class="brand">
    <span class="brand__square"></span>
    <p class="brand__name">GREYMARSH CONTRACTS</p>
  </div>
  <p class="tagline">Engineered to Excellence</p>
</section>

</body>
</html>
```